Harborline Auto LLC

Car Dealer Customer Service
Address: 2874 Cresthaven Road, Larkmoor Falls, KX 40162
web: www.harborlineautoxq.net
email: harborlineautoxq@mailnest.example
Phone: (931) 555-0148
Phone: (629) 555-0173

```html
<!DOCTYPE html>
<html lang="en">
<head>
<meta charset="utf-8">
<title>Harborline Auto – Business Card</title>
<link rel="stylesheet" href="https://fonts.googleapis.com/css2?family=Poppins:wght@400;600;700&display=swap">
<style>
  :root {
    --page: #2b2b2d;
    --card: #1f2023;
    --card-edge: #26272a;
    --emboss: #121214;
    --blue: #2a8ccb;
    --gold: #e2ac3a;
    --text: #e6e6e8;
  }
  html, body {
    margin: 0;
    padding: 0;
    width: 1200px;
    height: 1138px;
    overflow: hidden;
    background: var(--page);
    font-family: "Poppins", sans-serif;
  }
  .card {
    position: absolute;
    left: 274px;
    width: 622px;
    height: 374px;
    border-radius: 16px;
    background: linear-gradient(160deg, var(--card-edge), var(--card));
    overflow: hidden;
  }
  .card--front { top: 186px; }
  .card--back { top: 608px; height: 376px; }

  .front__name {
    position: absolute;
    left: 0; right: 0;
    top: 150px;
    text-align: center;
    font-weight: 700;
    font-size: 40px;
    letter-spacing: 1px;
    color: var(--emboss);
  }
  .front__web {
    position: absolute;
    left: 0; right: 0;
    top: 330px;
    display: flex;
    justify-content: center;
    align-items: center;
    gap: 22px;
    font-size: 15px;
    color: var(--text);
  }
  .front__rule {
    width: 54px;
    height: 2px;
    background: var(--gold);
  }

  .back__ring {
    position: absolute;
    left: 344px;
    top: 20px;
    width: 320px;
    height: 320px;
  }
  .back__mark {
    position: absolute;
    left: 412px;
    top: 166px;
    width: 184px;
    text-align: center;
    font-weight: 700;
    font-size: 22px;
    line-height: 28px;
    color: var(--gold);
  }
  .back__company {
    position: absolute;
    left: 26px;
    top: 40px;
    margin: 0;
    font-weight: 700;
    font-size: 30px;
    letter-spacing: 0.5px;
    color: var(--blue);
  }
  .back__person {
    position: absolute;
    left: 26px;
    top: 152px;
  }
  .person__name {
    margin: 0;
    font-weight: 700;
    font-size: 23px;
    line-height: 1.2;
    color: var(--blue);
  }
  .person__role {
    margin: 0;
    font-size: 16px;
    color: var(--text);
  }
  .back__contact {
    position: absolute;
    left: 26px;
    top: 234px;
    margin: 0;
    padding: 0;
    list-style: none;
    font-size: 16px;
    line-height: 22px;
    color: var(--text);
  }
  .contact__row {
    display: flex;
    align-items: center;
    gap: 10px;
  }
  .contact__row--phone {
    font-weight: 600;
    color: var(--blue);
    letter-spacing: 0.5px;
  }
  .contact__icon { width: 15px; height: 15px; flex: none; }
  .contact__address { margin-top: 4px; }
</style>
</head>
<body>

<section class="card card--front">
  <div class="front__name">Harborline Auto</div>
  <div class="front__web">
    <span class="front__rule"></span>
    <span>www.harborlineautoxq.net</span>
    <span class="front__rule"></span>
  </div>
</section>

<section class="card card--back">
  <svg class="back__ring" viewBox="0 0 320 320" aria-hidden="true">
    <circle cx="160" cy="160" r="120" fill="none" stroke="var(--blue)" stroke-width="56"/>
  </svg>
  <div class="back__mark">HARBORLINE</div>

  <h1 class="back__company">HARBORLINE AUTO</h1>

  <div class="back__person">
    <p class="person__name">Darren Kollwitz</p>
    <p class="person__role">Managing Director</p>
  </div>

  <ul class="back__contact">
    <li class="contact__row contact__row--phone">
      <svg class="contact__icon" viewBox="0 0 16 16"><path fill="var(--gold)" d="M1 5c2-3 12-3 14 0l-3 1-1-2H5L4 6zM4 7h8l2 7H2z"/></svg>
      555-555-0148
    </li>
    <li class="contact__row contact__row--phone">
      <svg class="contact__icon" viewBox="0 0 16 16"><path fill="var(--gold)" d="M1 5c2-3 12-3 14 0l-3 1-1-2H5L4 6zM4 7h8l2 7H2z"/></svg>
      555-555-0173
    </li>
    <li class="contact__row">
      <svg class="contact__icon" viewBox="0 0 16 16"><rect x="1" y="3" width="14" height="10" fill="var(--gold)"/><path d="M1 3l7 6 7-6" fill="none" stroke="var(--card)" stroke-width="1.4"/></svg>
      www.harborlineautoxq.net
    </li>
    <li class="contact__row">
      <svg class="contact__icon" viewBox="0 0 16 16"><circle cx="8" cy="8" r="6.5" fill="none" stroke="var(--gold)" stroke-width="1.5"/><path d="M1.5 8h13M8 1.5c-3 3-3 10 0 13M8 1.5c3 3 3 10 0 13" fill="none" stroke="var(--gold)" stroke-width="1.2"/></svg>
      harborlineautoxq@mailnest.example
    </li>
    <li class="contact__address">2874 Cresthaven Road, Larkmoor Falls, KX 40162</li>
  </ul>
</section>

</body>
</html>
```